Animal Eye Clinic needs a Business card

We are a new veterinary ophthalmology practice (Ridgeline Pet Vision Care) and we need a business card designed. We only see animal eyes - we are not a regular veterinary clinic. We already have a logo. We are looking for a professional, good looking business card to hand out to our clients. We are looking for something simple but professional and contemporary. Our logo is likely the only picture/graphic that needs to be on the card.
Updates

Contact Information for Business Card

Delia Vossman, BSc, DVM, MSc, DipACVO
Veterinary Ophthalmologist

Phone: 250.418.3927
Email: ridgelinepetvisioncare@mailbox-example.net
Website: ridgelinepetvisioncare-example.net
Address: 1874 Thornbury Rd
Kelowna, BC, V1X 4M9

Colors

Designer to choose colors to be used in the design.

Requirements
Must have
• Our logo (attached)

```html
<!DOCTYPE html>
<html lang="en">
<head>
<meta charset="utf-8">
<title>Ridgeline Pet Vision Care – Business Card</title>
<link rel="stylesheet" href="https://fonts.googleapis.com/css2?family=Open+Sans:ital,wght@0,400;0,600;0,700;1,700&display=swap">
<style>
  :root {
    --teal: #0e97a8;
    --teal-deep: #0a8594;
    --paper: #ffffff;
    --ink: #4a4a4a;
    --ink-soft: #6d6d6d;
    --rule: #8a8a8a;
    --ghost: #ececec;
    --stage: #2e2e2e;
  }
  * { box-sizing: border-box; margin: 0; padding: 0; }
  html, body {
    width: 1200px; height: 866px; overflow: hidden;
    background: var(--stage);
    font-family: "Open Sans", Arial, sans-serif;
  }
  .sheet {
    width: 1200px; height: 866px;
    display: flex; flex-direction: column; align-items: center; justify-content: center;
    gap: 40px;
  }
  .card {
    position: relative;
    width: 640px; height: 366px;
    overflow: hidden;
    box-shadow: 0 10px 24px rgba(0,0,0,.45);
  }
  /* Front */
  .card--front { background: var(--paper); }
  .card--front::after {
    content: ""; position: absolute; left: 0; right: 0; bottom: 0; height: 9px;
    background: var(--teal);
  }
  .artwork-area {
    position: absolute; left: 40px; top: 18px; width: 290px; height: 190px;
    border-radius: 48% 52% 40% 46%;
    background: radial-gradient(ellipse at 55% 45%, #e6e6e6 0%, #efefef 55%, rgba(255,255,255,0) 75%);
  }
  .brand {
    position: absolute; left: 300px; top: 108px;
    display: flex; align-items: center; gap: 12px;
  }
  .brand__dot {
    width: 46px; height: 46px; border-radius: 50%; background: var(--teal); flex: none;
  }
  .brand__name {
    color: var(--teal); font-weight: 700; font-size: 19px; line-height: 1.15;
    letter-spacing: 1px; text-transform: uppercase;
  }
  .person {
    position: absolute; left: 38px; top: 176px;
  }
  .person__name {
    color: var(--teal); font-weight: 700; font-style: italic; font-size: 17px;
    text-transform: uppercase; letter-spacing: .3px;
  }
  .person__creds {
    color: var(--ink-soft); font-weight: 400; font-style: normal; font-size: 12px;
    text-transform: none;
  }
  .person__title { color: var(--ink); font-size: 13px; margin-top: 1px; }
  .contact { list-style: none; margin-top: 8px; }
  .contact li {
    display: flex; align-items: center; gap: 7px;
    color: var(--ink); font-size: 12.5px; line-height: 19px;
  }
  .contact svg { width: 11px; height: 11px; fill: var(--teal); flex: none; }
  .divider {
    position: absolute; left: 222px; top: 226px; width: 386px; height: 1px;
    background: var(--rule);
  }
  .address {
    position: absolute; right: 34px; bottom: 34px; text-align: right;
    color: var(--ink); font-size: 13.5px; line-height: 20px;
  }
  /* Back */
  .card--back {
    background: var(--teal);
    display: flex; align-items: center; justify-content: center;
  }
  .card--back .brand { position: static; gap: 16px; }
  .card--back .brand__dot { width: 62px; height: 62px; background: var(--paper); }
  .card--back .brand__name { color: var(--paper); font-size: 26px; }
</style>
</head>
<body>
<main class="sheet">
  <section class="card card--front" aria-label="Business card front">
    <div class="artwork-area" role="img" aria-label="Faint grey illustration of animal heads"></div>

    <div class="brand">
      <span class="brand__dot"></span>
      <p class="brand__name">Ridgeline<br>Pet Vision Care</p>
    </div>

    <div class="person">
      <p class="person__name">Delia Vossman<span class="person__creds">, BSc, DVM, MSc, DipACVO</span></p>
      <p class="person__title">Veterinary Ophthalmologist</p>
      <ul class="contact">
        <li>
          <svg viewBox="0 0 16 16" aria-hidden="true"><path d="M3 1h3l1.5 4-2 1.3a9 9 0 0 0 4.2 4.2L11 8.5l4 1.5v3a2 2 0 0 1-2 2A12 12 0 0 1 1 3a2 2 0 0 1 2-2z"/></svg>
          250.418.3927
        </li>
        <li>
          <svg viewBox="0 0 16 16" aria-hidden="true"><path d="M1 3h14v10H1z M2 4v.4l6 4.2 6-4.2V4z" fill-rule="evenodd"/></svg>
          ridgelinepetvisioncare@mailbox-example.net
        </li>
        <li>
          <svg viewBox="0 0 16 16" aria-hidden="true"><circle cx="8" cy="8" r="7"/></svg>
          ridgelinepetvisioncare-example.net
        </li>
      </ul>
    </div>

    <div class="divider"></div>

    <address class="address" style="font-style:normal">
      1874 Thornbury Rd<br>
      Kelowna, BC, V1X 4M9
    </address>
  </section>

  <section class="card card--back" aria-label="Business card back">
    <div class="brand">
      <span class="brand__dot"></span>
      <p class="brand__name">Ridgeline<br>Pet Vision Care</p>
    </div>
  </section>
</main>
</body>
</html>
```